Business Card Design (NEW FILES)

ATTENTION: New vector files are available. Please update your design to reflect/use the new (better resolution) logo images.

Seeking a unique and professional business card design for a commercial drone photography/videography business. The layout should feature
the logo (attached) and include the following information:
Owen Tarrick
614-502-7738
www.skylarkreelworks.example
NRD Certified Remote Pilot

Owen Tarrick

```html
<!DOCTYPE html>
<html lang="en">
<head>
<meta charset="utf-8">
<title>Skylark Reelworks – Business Card</title>
<link rel="stylesheet" href="https://fonts.googleapis.com/css2?family=Open+Sans:wght@400;600;800&display=swap">
<style>
  :root {
    --stage: #232323;
    --navy: #1b1e5c;
    --navy-deep: #15174a;
    --navy-light: #2a3184;
    --orange: #e8894a;
    --paper: #ffffff;
    --ink: #1b1e5c;
    --ghost: #f1f2f5;
  }
  * { margin: 0; padding: 0; box-sizing: border-box; }
  html, body {
    width: 1200px;
    height: 780px;
    overflow: hidden;
    background: var(--stage);
    font-family: "Open Sans", Arial, sans-serif;
  }
  .canvas {
    position: relative;
    width: 1200px;
    height: 780px;
  }
  .card {
    position: absolute;
    width: 540px;
    height: 316px;
    border-radius: 22px;
    border: 4px solid var(--orange);
    overflow: hidden;
  }
  .card-back {
    left: 60px;
    top: 80px;
    background: var(--navy-deep);
  }
  .back-pattern {
    position: absolute;
    inset: 0;
    background: radial-gradient(ellipse at 70% 30%, var(--navy-light) 0%, var(--navy) 45%, var(--navy-deep) 100%);
  }
  .back-brand {
    position: absolute;
    right: 40px;
    bottom: 44px;
    display: flex;
    align-items: center;
    gap: 8px;
    color: var(--paper);
    font-weight: 600;
    font-size: 15px;
    letter-spacing: 0.5px;
  }
  .brand-dot {
    width: 10px;
    height: 10px;
    border-radius: 50%;
    background: var(--orange);
  }
  .card-front {
    left: 600px;
    top: 384px;
    background: var(--paper);
  }
  .front-watermark {
    position: absolute;
    left: 200px;
    top: 40px;
    width: 300px;
    height: 250px;
    border-radius: 50%;
    background: radial-gradient(ellipse at center, var(--ghost) 0%, rgba(241,242,245,0) 70%);
  }
  .front-brand {
    position: absolute;
    left: 34px;
    top: 150px;
    display: flex;
    align-items: center;
    gap: 10px;
    color: var(--ink);
    font-weight: 600;
    font-size: 26px;
    letter-spacing: 0.5px;
  }
  .front-brand .brand-dot { width: 14px; height: 14px; }
  .name-bar {
    position: absolute;
    right: 0;
    top: 40px;
    width: 18px;
    height: 48px;
    background: var(--orange);
  }
  .details {
    position: absolute;
    right: 30px;
    top: 38px;
    text-align: right;
    color: var(--ink);
  }
  .person-name {
    font-weight: 800;
    font-size: 30px;
    line-height: 1.05;
  }
  .person-name .first { color: var(--orange); }
  .person-role {
    font-weight: 600;
    font-size: 13px;
    margin-bottom: 22px;
  }
  .credential {
    font-weight: 600;
    font-size: 13px;
    line-height: 1.4;
  }
  .contact-list {
    list-style: none;
    margin-top: 20px;
  }
  .contact-item {
    display: flex;
    justify-content: flex-end;
    align-items: center;
    gap: 8px;
    font-weight: 600;
    font-size: 13px;
    line-height: 1.6;
  }
  .contact-icon { width: 13px; height: 13px; }
</style>
</head>
<body>
<main class="canvas">
  <section class="card card-back">
    <div class="back-pattern" role="img" aria-label="Repeating embossed drone pattern on navy"></div>
    <div class="back-brand"><span class="brand-dot"></span>Skylark Reelworks</div>
  </section>

  <section class="card card-front">
    <div class="front-watermark" role="img" aria-label="Faint embossed drone outline decoration"></div>
    <div class="front-brand"><span class="brand-dot"></span>Skylark Reelworks</div>
    <div class="name-bar"></div>
    <div class="details">
      <h1 class="person-name"><span class="first">Owen</span> Tarrick</h1>
      <p class="person-role">Owner</p>
      <p class="credential">NRD Certified Remote Pilot</p>
      <p class="credential">Fully Insured</p>
      <ul class="contact-list">
        <li class="contact-item">614-502-7738
          <svg class="contact-icon" viewBox="0 0 24 24" aria-hidden="true"><path fill="#e8894a" d="M6.6 10.8a15.1 15.1 0 0 0 6.6 6.6l2.2-2.2c.3-.3.7-.4 1-.2 1.1.4 2.3.6 3.6.6.6 0 1 .4 1 1V20c0 .6-.4 1-1 1A17 17 0 0 1 3 4c0-.6.4-1 1-1h3.5c.6 0 1 .4 1 1 0 1.3.2 2.5.6 3.6.1.3 0 .7-.2 1z"/></svg>
        </li>
        <li class="contact-item">www.skylarkreelworks.example
          <svg class="contact-icon" viewBox="0 0 24 24" aria-hidden="true"><circle cx="12" cy="12" r="10" fill="none" stroke="#e8894a" stroke-width="2"/><path d="M2 12h20M12 2c3 3 3 17 0 20M12 2c-3 3-3 17 0 20" fill="none" stroke="#e8894a" stroke-width="1.6"/></svg>
        </li>
      </ul>
    </div>
  </section>
</main>
</body>
</html>
```